Modern 10’x10’ Dog Product Trade Show Booth Tent

We need a 10’x10’ trade show / vendor tent designed for our pet product company, #KELO™. Our flagship product is a new and revolutionary no-pull dog harness. We are looking for a design that is in the spirit of our brand and most importantly, compliments our product and packaging; as our products and packaging will be displayed in the booth.

The sections we need designed are the top (canopy) of the tent, back wall, half-sides, and table covers.

Our brand style is modern and our color palate focuses on bright neon colors on dark (black or dark navy) background. Our website is www.hashkeloshop.example

Please refer to the uploaded files for packaging images, and our website for brand style.

Many many thanks in advance to all who submit designs. You are very appreciated.
Updates

Only submissions for 10’x10’ tents will be considered. Not lone backdrops

Target Market(s)

Dog owning young adults and dog owning families

Industry/Entity Type

Dog accessories retailer

Font styles to use
Sans Serif

Requirements
Must have
• Company logo, and company website
Nice to have
• Other dog related graphics

```html
<!DOCTYPE html>
<html lang="en">
<head>
<meta charset="utf-8">
<title>#KELO™ Booth Tent Panels</title>
<link rel="stylesheet" href="https://fonts.googleapis.com/css2?family=Montserrat:ital,wght@0,500;0,700;0,900;1,700&display=swap">
<style>
  :root {
    --stage: #dcdce1;
    --navy: #0d1326;
    --navy-soft: #151d36;
    --neon-green: #39ff7a;
    --neon-pink: #ff3d9a;
    --ink-white: #f5f7fb;
    --frame-line: rgba(57, 255, 122, 0.45);
    --fur-light: #cbb79c;
    --fur-dark: #7f766c;
    --harness-a: #2b2f3d;
    --harness-b: #39ff7a;
  }
  * { margin: 0; padding: 0; box-sizing: border-box; }
  html, body { width: 1200px; height: 1000px; overflow: hidden; background: var(--stage); }
  body { font-family: "Montserrat", sans-serif; }
  .canvas { position: relative; width: 1200px; height: 1000px; }

  .panel { position: absolute; background: var(--navy); overflow: hidden; }
  .panel-frame { position: absolute; inset: 14px; border: 1.5px solid var(--frame-line); pointer-events: none; }

  .title {
    position: absolute; font-weight: 900; color: var(--ink-white);
    line-height: 1.02; letter-spacing: 0.01em; text-transform: uppercase;
  }
  .title span { display: block; }
  .title .accent { color: var(--neon-green); }
  .title .last { text-align: right; color: var(--neon-pink); }

  .brand-mark {
    position: absolute; font-weight: 900; white-space: nowrap; color: var(--neon-green);
    line-height: 1;
  }
  .brand-mark .dot { display: inline-block; width: 0.4em; height: 0.4em; background: currentColor; margin-left: 0.3em; vertical-align: middle; }
  .brand-mark.vertical { writing-mode: vertical-rl; transform: rotate(180deg); }
  .brand-mark.vertical .dot { margin-left: 0; margin-top: 0.3em; }

  .website {
    position: absolute; font-weight: 700; color: var(--neon-green);
    white-space: nowrap; letter-spacing: 0.02em;
  }

  .dog-photo {
    position: absolute;
    background: linear-gradient(120deg, var(--fur-light) 0%, #a99a86 55%, var(--fur-dark) 100%);
    border-radius: 0 46% 30% 0 / 0 55% 40% 0;
  }
  .harness-photo {
    position: absolute; border-radius: 14px;
    background: linear-gradient(135deg, var(--harness-a) 0%, var(--harness-a) 55%, var(--harness-b) 100%);
    border: 2px solid var(--neon-green);
  }

  .bubble {
    position: absolute; background: var(--navy-soft);
    border: 2px dashed var(--neon-pink); border-radius: 48% 52% 46% 54% / 55% 48% 52% 45%;
    color: var(--ink-white); text-align: center;
    display: flex; flex-direction: column; justify-content: center; align-items: center;
  }
  .bubble .line { font-weight: 700; font-style: italic; line-height: 1.15; }
  .bubble .tag { font-weight: 900; color: var(--neon-green); letter-spacing: 0.04em; margin-top: 2px; }

  .back-wall { left: 40px; top: 40px; width: 620px; height: 470px; }
  .canopy { left: 700px; top: 40px; width: 460px; height: 460px; }
  .canopy-edge { position: absolute; font-weight: 900; font-size: 15px; color: var(--ink-white); white-space: nowrap; letter-spacing: 0.04em; }
  .canopy-edge.side { writing-mode: vertical-rl; }
  .half-wall { left: 40px; top: 540px; width: 620px; height: 230px; }
  .table-cover { left: 700px; top: 540px; width: 460px; height: 420px; }
</style>
</head>
<body>
<main class="canvas">

  <section class="panel back-wall">
    <div class="panel-frame"></div>
    <h1 class="title" style="left:40px; top:40px; font-size:50px;">
      <span>THE</span><span class="accent">STRIDELOCK</span><span class="last">HARNESS</span>
    </h1>
    <div class="brand-mark vertical" style="right:40px; top:40px; font-size:34px;">#KELO™<span class="dot"></span></div>
    <div class="dog-photo" role="img" aria-label="Photo of a golden retriever wearing the no-pull harness" style="left:0; top:260px; width:300px; height:210px;"></div>
    <div class="harness-photo" role="img" aria-label="Photo of the no-pull harness product" style="left:250px; top:362px; width:80px; height:70px;"></div>
    <div class="bubble" style="left:350px; top:270px; width:220px; height:120px;">
      <span class="line" style="font-size:19px;">Ridiculously comfy</span>
      <span class="line" style="font-size:19px;">no-pull</span>
      <span class="tag" style="font-size:20px;">HARNESS</span>
    </div>
    <div class="website" style="right:40px; bottom:30px; font-size:15px;">www.hashkeloshop.example</div>
  </section>

  <section class="panel canopy">
    <div class="canopy-edge" style="left:50%; top:16px; transform:translateX(-50%) rotate(180deg);">THE STRIDELOCK HARNESS</div>
    <div class="canopy-edge" style="left:50%; bottom:16px; transform:translateX(-50%);">THE STRIDELOCK HARNESS</div>
    <div class="canopy-edge side" style="left:16px; top:50%; transform:translateY(-50%);">THE STRIDELOCK HARNESS</div>
    <div class="canopy-edge side" style="right:16px; top:50%; transform:translateY(-50%) rotate(180deg);">THE STRIDELOCK HARNESS</div>

    <div class="brand-mark" style="left:50%; top:90px; font-size:28px; transform:translateX(-50%) rotate(180deg);">#KELO™<span class="dot"></span></div>
    <div class="brand-mark" style="left:50%; bottom:90px; font-size:28px; transform:translateX(-50%);">#KELO™<span class="dot"></span></div>
    <div class="brand-mark vertical" style="left:90px; top:50%; font-size:28px; transform:translateY(-50%);">#KELO™<span class="dot"></span></div>
    <div class="brand-mark vertical" style="right:90px; top:50%; font-size:28px; transform:translateY(-50%) rotate(180deg);">#KELO™<span class="dot"></span></div>

    <div class="website" style="left:50%; top:50%; transform:translate(-50%,-50%); font-size:13px; color:var(--neon-pink);">www.hashkeloshop.example</div>
  </section>

  <section class="panel half-wall">
    <div class="dog-photo" role="img" aria-label="Photo of a golden retriever wearing the no-pull harness" style="left:0; top:20px; width:200px; height:210px;"></div>
    <h2 class="title" style="left:230px; top:30px; font-size:38px;">
      <span>THE</span><span class="accent">STRIDELOCK</span><span class="last">HARNESS</span>
    </h2>
    <div class="brand-mark vertical" style="right:26px; top:24px; font-size:24px;">#KELO™<span class="dot"></span></div>
    <div class="website" style="left:230px; bottom:20px; font-size:13px;">www.hashkeloshop.example</div>
  </section>

  <section class="panel table-cover">
    <div class="panel-frame"></div>
    <h2 class="title" style="left:36px; top:36px; font-size:32px;">
      <span>THE</span><span class="accent">STRIDELOCK</span><span class="last">HARNESS</span>
    </h2>
    <div class="brand-mark vertical" style="right:36px; top:36px; font-size:26px;">#KELO™<span class="dot"></span></div>
    <div class="dog-photo" role="img" aria-label="Photo of a golden retriever wearing the no-pull harness" style="left:0; top:200px; width:200px; height:220px;"></div>
    <div class="harness-photo" role="img" aria-label="Photo of the no-pull harness product" style="left:165px; top:300px; width:80px; height:70px;"></div>
    <div class="bubble" style="left:245px; top:190px; width:185px; height:110px;">
      <span class="line" style="font-size:16px;">Ridiculously comfy</span>
      <span class="line" style="font-size:16px;">no-pull</span>
      <span class="tag" style="font-size:17px;">HARNESS</span>
    </div>
    <div class="website" style="right:36px; bottom:30px; font-size:13px;">www.hashkeloshop.example</div>
  </section>

</main>
</body>
</html>
```